Business cards and stationary design

We just completed the design of our new logo and we need to print new business cards and letterhead for our nonprofit. We are looking for a fresh new design that shows off our new logo. On letterhead, we must have a column on the right or left to include our Board of Directors (up to 45 names) (see attachment)

Industry/Entity Type

Non-Profit

Contact Information for Business Card

Standard business card with name, title, Company name, mailing address phone numbers, email address and website. Tagline on back "Bringing the homeless home"

Font styles to use
Sans Serif

Requirements
Must have
• include pertinent information above
• new logo
• fonts compatible with logo
• should use logo colors only
Nice to have
• tag lines

```html
<!DOCTYPE html>
<html lang="en">
<head>
<meta charset="utf-8">
<title>Harbor Home Alliance – Business Card</title>
<link rel="stylesheet" href="https://fonts.googleapis.com/css2?family=Michroma&family=Ubuntu:wght@400&display=swap">
<style>
  :root {
    --page-bg: #d8d3cb;
    --band-top: #1f6580;
    --band-bottom: #0e3a52;
    --gold: #e2a22b;
    --red: #b3302e;
    --navy: #1b4964;
    --teal: #1f5f7c;
    --card-top: #f1f3f4;
    --card-bottom: #e3e6e8;
    --ink: #1a1a1a;
  }
  * { box-sizing: border-box; margin: 0; padding: 0; }
  html, body { width: 1200px; height: 969px; overflow: hidden; }
  body { background: var(--page-bg); position: relative; }

  .business-card {
    position: absolute; left: 100px; top: 200px;
    width: 1000px; height: 570px;
    background: linear-gradient(180deg, var(--card-top), var(--card-bottom));
    box-shadow: 0 18px 40px rgba(0,0,0,.18);
    overflow: hidden;
  }
  .header-band {
    position: absolute; left: 0; top: 0; width: 100%; height: 166px;
    background: linear-gradient(180deg, var(--band-top), var(--band-bottom));
    text-align: center;
  }
  .holder-name {
    position: absolute; top: 60px; width: 100%;
    font-family: "Michroma", sans-serif; font-size: 30px; letter-spacing: 3px;
    color: var(--gold);
  }
  .holder-title {
    position: absolute; top: 104px; width: 100%;
    font-family: "Michroma", sans-serif; font-size: 17px; letter-spacing: 3px;
    color: var(--gold);
  }
  .rule-light { position: absolute; left: 0; top: 168px; width: 100%; height: 4px; background: #fff; }
  .rule-navy { position: absolute; left: 0; top: 175px; width: 930px; height: 4px; background: var(--navy); }
  .rule-accent { position: absolute; left: 930px; top: 170px; width: 70px; height: 12px; background: var(--red); }
  .corner-mark { position: absolute; left: 896px; top: 146px; width: 26px; height: 26px; background: var(--gold); }

  .brand {
    position: absolute; left: 60px; top: 300px; width: 480px; text-align: center;
  }
  .brand-dot {
    width: 64px; height: 64px; border-radius: 50%; background: var(--gold);
    margin: 0 auto 28px;
  }
  .brand-name {
    font-family: "Michroma", sans-serif; font-size: 27px; letter-spacing: 2px;
    color: var(--teal); line-height: 1.3;
  }

  .contact {
    position: absolute; left: 562px; top: 276px;
    font-family: "Ubuntu", sans-serif; color: var(--ink);
  }
  .address { font-size: 23px; line-height: 30px; margin-bottom: 14px; }
  .contact-row {
    display: flex; align-items: center; gap: 14px;
    font-size: 20px; line-height: 32px;
  }
  .contact-row svg { width: 20px; height: 20px; fill: var(--ink); flex: none; }
</style>
</head>
<body>
  <div class="business-card">
    <header class="header-band">
      <div class="holder-name">DANIEL REYES</div>
      <div class="holder-title">CEO/FOUNDER</div>
    </header>
    <div class="rule-light"></div>
    <div class="rule-navy"></div>
    <div class="rule-accent"></div>
    <div class="corner-mark"></div>

    <div class="brand">
      <div class="brand-dot"></div>
      <div class="brand-name">HARBOR HOME<br>ALLIANCE</div>
    </div>

    <div class="contact">
      <p class="address">Harbor Home Alliance<br>2140 Birchwood Court<br>Juneau, Alaska 99801</p>
      <div class="contact-row">
        <svg viewBox="0 0 24 24" aria-hidden="true"><path d="M6.6 10.8a15.1 15.1 0 0 0 6.6 6.6l2.2-2.2c.3-.3.7-.4 1-.2 1.1.4 2.3.6 3.6.6.6 0 1 .4 1 1V20c0 .6-.4 1-1 1A17 17 0 0 1 3 4c0-.6.4-1 1-1h3.5c.6 0 1 .4 1 1 0 1.3.2 2.5.6 3.6.1.3 0 .7-.2 1z"/></svg>
        <span>555 214 7730</span>
      </div>
      <div class="contact-row">
        <svg viewBox="0 0 24 24" aria-hidden="true"><path d="M2 5h20v14H2zm2 2v.4l8 5 8-5V7zm0 2.8V17h16V9.8l-8 5z"/></svg>
        <span>daniel@harborhomealliance.org</span>
      </div>
      <div class="contact-row">
        <svg viewBox="0 0 24 24" aria-hidden="true"><path d="M12 2a10 10 0 1 0 0 20 10 10 0 0 0 0-20zm6.9 6h-3a15 15 0 0 0-1.3-3.9A8 8 0 0 1 18.9 8zM12 4c.8 1.2 1.5 2.5 1.9 4h-3.8c.4-1.5 1.1-2.8 1.9-4zM4.3 14a8 8 0 0 1 0-4h3.4a16 16 0 0 0 0 4zm.8 2h3a15 15 0 0 0 1.3 3.9A8 8 0 0 1 5.1 16zm3-8h-3a8 8 0 0 1 4.3-3.9C8.8 5.3 8.4 6.6 8.1 8zM12 20c-.8-1.2-1.5-2.5-1.9-4h3.8c-.4 1.5-1.1 2.8-1.9 4zm2.3-6H9.7a14 14 0 0 1 0-4h4.6a14 14 0 0 1 0 4zm.3 5.9c.6-1.2 1-2.5 1.3-3.9h3a8 8 0 0 1-4.3 3.9zm1.7-5.9a16 16 0 0 0 0-4h3.4a8 8 0 0 1 0 4z"/></svg>
        <span>www.harborhomealliance.org</span>
      </div>
    </div>
  </div>
</body>
</html>
```